Chimney Service company needs new business card design

We need a updated business card with our new logo added. We provide a full range of chimney services throughout Vermont and New Hampshire. The business card will be one sided and color. Attached is our current business card another document showing all the information we would like on the card.
We dont like a lot of flashy colors.... here is a link to our website to get an idea of our branding www.flueguardianvt.example

Target Market(s)

homeowners

Industry/Entity Type

Business

Contact Information for Business Card

See attached sheet for content.

Font styles to use
Serif
Sans Serif

Requirements
Must have
• all information provided on separate sheet
Should not have
• Additional information that may clogg up design

```html
<!DOCTYPE html>
<html lang="en">
<head>
<meta charset="utf-8">
<title>Flue Guardian – Business Card</title>
<link rel="stylesheet" href="https://fonts.googleapis.com/css2?family=Open+Sans:wght@400;600;800&display=swap">
<style>
  :root {
    --backdrop: #2e2e30;
    --card-black: #161617;
    --card-charcoal: #262627;
    --brand-red: #d4221c;
    --white: #ffffff;
    --soft-grey: #9a9a9c;
    --emboss: #4a4a4d;
  }
  * { margin: 0; padding: 0; box-sizing: border-box; }
  html, body { width: 799px; height: 1200px; overflow: hidden; }
  body {
    background: var(--backdrop);
    font-family: "Open Sans", sans-serif;
    display: flex;
    flex-direction: column;
    align-items: center;
    justify-content: center;
    gap: 110px;
  }
  .card {
    position: relative;
    width: 640px;
    height: 366px;
    overflow: hidden;
    box-shadow: 0 14px 30px rgba(0,0,0,.45);
  }

  /* Front */
  .card-front { background: var(--card-black); }
  .front-name {
    position: absolute;
    inset: 0;
    display: flex;
    align-items: center;
    justify-content: center;
    font-weight: 600;
    font-size: 36px;
    letter-spacing: 2px;
    color: var(--emboss);
  }

  /* Back */
  .card-back { background: var(--card-charcoal); color: var(--white); }
  .back-panel { position: absolute; inset: 0; }
  .back-name {
    position: absolute;
    left: 32px;
    top: 118px;
    font-weight: 600;
    font-size: 26px;
    letter-spacing: 1px;
    color: var(--white);
  }
  .service-list {
    position: absolute;
    left: 32px;
    top: 178px;
    list-style: none;
    font-size: 13.5px;
    line-height: 20px;
  }
  .service-list li { display: flex; align-items: center; gap: 9px; }
  .service-list li::before {
    content: "";
    width: 7px; height: 9px;
    background: var(--brand-red);
    clip-path: polygon(50% 0, 100% 100%, 0 100%);
  }
  .promise-list {
    position: absolute;
    right: 26px;
    top: 54px;
    list-style: none;
    text-align: right;
    font-size: 12.5px;
    line-height: 18px;
    color: var(--white);
  }
  .service-area {
    position: absolute;
    right: 40px;
    top: 232px;
  }
  .service-area h2 {
    font-weight: 800;
    font-size: 20px;
    line-height: 21px;
    text-transform: uppercase;
  }
  .since {
    display: flex;
    align-items: center;
    gap: 8px;
    font-size: 9px;
    letter-spacing: 1px;
    color: var(--soft-grey);
    margin-top: 4px;
  }
  .since::before, .since::after {
    content: ""; flex: 1; height: 2px; background: var(--brand-red);
  }
  .contact-list {
    position: absolute;
    right: 26px;
    bottom: 14px;
    list-style: none;
    text-align: right;
    font-size: 13px;
    line-height: 20px;
  }
  .contact-list li { display: flex; align-items: center; justify-content: flex-end; gap: 8px; }
  .contact-list svg { width: 12px; height: 12px; fill: var(--brand-red); }
  .accent { color: var(--brand-red); }
</style>
</head>
<body>

<section class="card card-front" aria-label="Card front">
  <p class="front-name">FLUE GUARDIAN</p>
</section>

<section class="card card-back" aria-label="Card back">
  <svg class="back-panel" viewBox="0 0 640 366" preserveAspectRatio="none" aria-hidden="true">
    <polygon points="180,0 640,0 640,210" fill="var(--brand-red)"/>
    <line x1="150" y1="0" x2="640" y2="224" stroke="var(--white)" stroke-width="3"/>
  </svg>

  <p class="back-name">FLUE GUARDIAN</p>

  <ul class="service-list">
    <li>Full Masonry Services</li>
    <li>Historic chimney restoration</li>
    <li>Stainless steel liners</li>
    <li>New Chimney installations</li>
    <li>Certified Chimney sweeps</li>
  </ul>

  <ul class="promise-list">
    <li>Fully Insured &amp; Free Estimates «</li>
    <li>Family Owned &amp; Operated «</li>
  </ul>

  <div class="service-area">
    <h2>Serving VT and<br>New Hampshire</h2>
    <p class="since">SINCE 2004</p>
  </div>

  <ul class="contact-list">
    <li>802-555-0147
      <svg viewBox="0 0 24 24" aria-hidden="true"><path d="M6.6 10.8a15 15 0 0 0 6.6 6.6l2.2-2.2c.3-.3.7-.4 1-.2 1.1.4 2.3.6 3.6.6.6 0 1 .4 1 1V20c0 .6-.4 1-1 1A17 17 0 0 1 3 4c0-.6.4-1 1-1h3.5c.6 0 1 .4 1 1 0 1.3.2 2.5.6 3.6.1.3 0 .7-.2 1z"/></svg>
    </li>
    <li>info@flueguardianvt.example
      <svg viewBox="0 0 24 24" aria-hidden="true"><path d="M2 5h20v14H2z M4 7v.4l8 5 8-5V7l-8 5z" fill-rule="evenodd"/></svg>
    </li>
    <li><span>www.<span class="accent">flueguardianvt</span>.example</span>
      <svg viewBox="0 0 24 24" aria-hidden="true"><circle cx="12" cy="12" r="10"/><path d="M2 12h20M12 2c3 3 3 17 0 20M12 2c-3 3-3 17 0 20" stroke="var(--card-charcoal)" stroke-width="1.6" fill="none"/></svg>
    </li>
  </ul>
</section>

</body>
</html>
```